EB-5 Regional Center needs a Web design

Harlow Ridge Financial Partners is an expanding EB-r regional center. We have been successful in sponsoring multiple projects of third-party developers and placing EB-5, B-1, and Private Investments into multiple projects.

We are now partnering directly with project developers in the energy and healthcare to raise foreign capital for projects in those industries. The foreign capital is used as project equity and our collective balance sheets are used to guarantee debt to complete the funding of the projects.

We need a web site where we can post our company credentials, the bios of each partner, a document page for each of our projects where we can post specific project related documents which foreign investors can read, and we will need a section where foreign investors can fill out investor forms confirming that they are qualified investors and leaving their contact so that our agents and executives can make contact.

The final design should reflect the exceptional experience of the partners and our financial strength and stability.

We do have a logo we would want to use on the web design.

Target Market(s)

EB-5 Investors, B-1 Investors, Private Equity and other investors seeking quality investment in job creating US projects.

Coding

Number of Pages Required

5+ page

Font styles to use
Sans Serif

Requirements
Must have
• Pages to display company info, partner bios, projects completed, and a projects in-process page where we can post documents and info on projects for which we are seeking foreign investment. We also need a section where investors can enter their qualifying personal information and leave contact information for us.

```html
<!DOCTYPE html>
<html lang="en">
<head>
<meta charset="utf-8">
<title>Harlow Ridge Financial Partners</title>
<link href="https://fonts.googleapis.com/css2?family=Poppins:wght@400;500;600;700&family=Raleway:wght@400;500;600&display=swap" rel="stylesheet">
<style>
:root{
  --orange:#f26a1b;
  --ink:#1d1d1d;
  --text:#555;
  --muted:#8a8a8a;
  --line:#dcdcdc;
  --dark:#232323;
  --footer:#262626;
  --light:#f4f4f4;
  --white:#fff;
}
*{box-sizing:border-box;margin:0;padding:0}
html,body{width:1200px;height:4910px;overflow:hidden}
body{position:relative;background:var(--white);font-family:"Raleway",sans-serif;color:var(--text)}
.abs{position:absolute}
.head-font{font-family:"Poppins",sans-serif}

/* header */
.site-header{position:absolute;left:0;top:0;width:1200px;height:105px;background:var(--white)}
.brand{position:absolute;left:114px;top:34px;display:flex;align-items:center;gap:12px}
.brand-mark{width:34px;height:34px;background:#6d6d6d}
.brand-name{font-family:"Poppins",sans-serif;font-weight:600;font-size:19px;color:#5d5d5d;line-height:1.1;width:220px}
.call{position:absolute;right:108px;top:16px;font-size:14px;color:#555;font-family:"Poppins",sans-serif}
.call b{font-size:20px;font-weight:500;color:#333}
.nav{position:absolute;right:108px;top:62px;display:flex;gap:27px;font-family:"Poppins",sans-serif;font-size:15px;color:#333}
.nav .active{color:var(--orange)}

/* hero */
.hero{position:absolute;left:0;top:105px;width:1200px;height:569px;background:linear-gradient(110deg,#5a5550 0%,#8d8780 35%,#b9b2a8 60%,#6f665d 100%)}
.hero-panel{position:absolute;left:259px;top:133px;width:636px;height:253px;background:rgba(255,255,255,.18)}
.hero h1{position:absolute;left:0;top:188px;width:1200px;text-align:center;font-family:"Poppins",sans-serif;font-weight:500;font-size:54px;color:var(--white);letter-spacing:-.5px}
.hero p{position:absolute;left:300px;top:254px;width:600px;text-align:center;font-size:14px;line-height:26px;color:var(--white)}
.btn{display:inline-block;background:var(--orange);color:var(--white);font-family:"Poppins",sans-serif;font-size:15px;text-align:center;border-radius:6px}
.hero .btn{position:absolute;left:517px;top:314px;width:146px;height:42px;line-height:42px}
.dots{position:absolute;left:530px;top:532px;display:flex;gap:14px}
.dots span{width:22px;height:3px;background:var(--orange);opacity:.7}

/* how */
.section-title{position:absolute;left:0;width:1200px;text-align:center;font-family:"Poppins",sans-serif;font-weight:500;font-size:38px;color:var(--ink)}
.steps{position:absolute;left:111px;top:846px;width:978px;height:316px;border:1px solid var(--line);display:flex}
.step{flex:1;text-align:center;border-right:1px solid var(--line);padding-top:20px}
.step:last-child{border-right:0}
.step svg{display:block;margin:0 auto}
.step h3{margin-top:36px;font-family:"Poppins",sans-serif;font-weight:500;font-size:14px;color:var(--ink)}
.step p{margin:14px auto 0;width:296px;font-size:14px;line-height:28px;color:var(--muted)}
.step a{display:inline-block;margin-top:12px;font-family:"Poppins",sans-serif;font-size:14px;color:var(--orange);text-decoration:underline}

/* services */
.services{position:absolute;left:0;top:1265px;width:1200px;height:636px;background:linear-gradient(100deg,#1e1e1e,#3a3835 50%,#1e1e1e)}
.services .section-title{color:var(--white);top:98px}
.service{position:absolute;width:330px;display:flex;gap:18px}
.diamond{width:76px;height:76px;flex:none;position:relative}
.diamond::before{content:"";position:absolute;left:11px;top:11px;width:54px;height:54px;background:var(--white);transform:rotate(45deg)}
.diamond svg{position:absolute;left:20px;top:20px}
.service h4{font-family:"Poppins",sans-serif;font-weight:500;font-size:14px;color:var(--white);margin-top:12px}
.service p{font-size:11.5px;line-height:23px;color:#ddd;margin-top:6px;width:210px}
.center-ring{position:absolute;left:434px;top:192px;width:336px;height:336px;border:2px dashed #ddd;border-radius:50%;display:flex;align-items:center;justify-content:center;text-align:center}
.center-ring span{font-family:"Poppins",sans-serif;font-weight:600;font-size:26px;line-height:34px;color:var(--white);width:220px}

/* projects */
.arrow-btn{position:absolute;width:48px;height:48px;border:1px solid #bbb;border-radius:50%;top:2154px}
.card{position:absolute;top:2071px;width:238px;height:257px;background:var(--white);box-shadow:0 2px 6px rgba(0,0,0,.12)}
.card .photo{height:213px}
.card p{text-align:center;font-family:"Poppins",sans-serif;font-weight:500;font-size:14px;color:var(--ink);line-height:44px}

/* help band */
.help{position:absolute;left:0;top:2437px;width:1200px;height:402px;background:linear-gradient(90deg,#4b5560 0%,#707880 45%,#8c8c88 70%,#4a4440 100%)}
.help .kicker{position:absolute;left:112px;top:94px;font-family:"Poppins",sans-serif;font-size:20px;color:var(--white)}
.help h2{position:absolute;left:112px;top:128px;font-family:"Poppins",sans-serif;font-weight:600;font-size:30px;color:var(--white)}
.help p{position:absolute;left:112px;top:186px;width:360px;font-size:14px;line-height:26px;color:var(--white)}
.help .btn{position:absolute;left:112px;top:250px;width:152px;height:46px;line-height:46px;border-radius:23px}

/* bios */
.bio-photo{position:absolute;width:600px;height:388px}
.bio{position:absolute;width:542px;height:296px;background:var(--white);box-shadow:0 2px 10px rgba(0,0,0,.15);padding:34px 80px 0 42px}
.bio.right-accent{border-right:5px solid var(--orange)}
.bio.left-accent{border-left:5px solid var(--orange)}
.bio h3{font-family:"Poppins",sans-serif;font-weight:500;font-size:19px;color:var(--ink)}
.bio .role{font-size:14px;color:#444;margin-top:2px}
.bio p{margin-top:20px;font-size:14px;line-height:30px;color:var(--muted);text-align:justify}
.socials{position:absolute;right:26px;top:54px;display:flex;flex-direction:column;gap:40px}
.socials span{width:12px;height:12px;border:1.5px solid #777;border-radius:50%}

/* contact */
.contact{position:absolute;left:0;top:3892px;width:1200px;height:558px;background:var(--light)}
.contact h2{position:absolute;left:112px;top:100px;width:380px;font-family:"Poppins",sans-serif;font-weight:600;font-size:29px;line-height:42px;color:var(--ink)}
.contact .lead{position:absolute;left:112px;top:250px;width:362px;font-size:14px;line-height:34px;color:var(--muted);text-align:justify}
.field{position:absolute;height:48px;border:1px solid #c8c8c8;border-radius:4px;background:var(--light);padding:14px 16px;font-size:14px;color:#888}
.forgot{position:absolute;left:562px;top:4364px;font-size:14px;color:#888}
.submit{position:absolute;left:825px;top:4353px;width:263px;height:44px;line-height:44px;border-radius:4px;font-weight:500}

/* footer */
.footer{position:absolute;left:0;top:4450px;width:1200px;height:460px;background:var(--footer);color:#ccc}
.footer h5{position:absolute;top:104px;font-family:"Poppins",sans-serif;font-weight:500;font-size:14px;color:var(--white)}
.links{position:absolute;top:146px;list-style:none;font-size:14px;line-height:34px;color:#ccc}
.c-item{position:absolute;left:554px;display:flex;align-items:center;gap:20px;font-size:14px;line-height:24px;width:340px}
.ring{width:38px;height:38px;border:1.5px solid #ddd;border-radius:50%;flex:none;display:flex;align-items:center;justify-content:center}
.s-item{position:absolute;left:947px;display:flex;align-items:center;gap:10px;font-size:14px}
.s-item .ring{width:32px;height:32px}
.copyright{position:absolute;left:0;top:411px;width:1200px;text-align:center;font-size:14px;color:#ccc}
</style>
</head>
<body>

<header class="site-header">
  <div class="brand"><div class="brand-mark"></div><div class="brand-name">Harlow Ridge Financial Partners</div></div>
  <div class="call">CALL US NOW - <b>555-014-2290</b></div>
  <nav class="nav"><span class="active">HOME</span><span>ABOUT US</span><span>SERVICES</span><span>PROJECTS</span><span>PARTNERS</span><span>CONTACT</span></nav>
</header>

<section class="hero" role="img" aria-label="Photo of advisors meeting with clients over a laptop in a bright office">
  <div class="hero-panel"></div>
  <h1>CAPITAL INVESTMENTS</h1>
  <p>Nemo enim ipsam voluptatem quia voluptas sit aspernatur aut odit aut fugit, sed quia consequuntur magni dolores</p>
  <span class="btn">GET STARTED</span>
  <div class="dots"><span></span><span></span><span></span><span></span></div>
</section>

<h2 class="section-title" style="top:762px">How does it work?</h2>
<div class="steps">
  <div class="step">
    <svg width="80" height="80" viewBox="0 0 80 80" fill="none" stroke="var(--orange)" stroke-width="3"><path d="M30 14h34v52H30"/><path d="M12 40h34M36 30l10 10-10 10"/></svg>
    <h3>SIGN UP TO GAIN FULL ACCESS</h3>
    <p>Nemo enim ipsam voluptatem quia voluptas sit aspernatur aut odit aut fugit, sed quia consequuntur magni dolores eos qui ratione voluptatem</p>
    <a>READ MORE</a>
  </div>
  <div class="step">
    <svg width="80" height="80" viewBox="0 0 80 80" fill="none" stroke="var(--orange)" stroke-width="3"><circle cx="40" cy="28" r="13"/><path d="M40 20v16M35 24h8a3 3 0 010 6h-6a3 3 0 000 6h8"/><path d="M10 58h14l10 4h16a4 4 0 000-8H38M24 54l12-6h8M10 52v14"/></svg>
    <h3>MAKE INVESTMENTS AT YOUR OWN PACE</h3>
    <p>Nemo enim ipsam voluptatem quia voluptas sit aspernatur aut odit aut fugit, sed quia consequuntur magni dolores eos qui ratione voluptatem</p>
    <a>READ MORE</a>
  </div>
  <div class="step">
    <svg width="90" height="80" viewBox="0 0 90 80" fill="none" stroke="var(--orange)" stroke-width="3"><rect x="8" y="22" width="74" height="42"/><path d="M20 56V40M32 56V32M44 56V26M56 56V36M68 56V30M4 68h82"/></svg>
    <h3>MANAGE YOUR INVESTMENTS ONLINE</h3>
    <p>Nemo enim ipsam voluptatem quia voluptas sit aspernatur aut odit aut fugit, sed quia consequuntur magni dolores eos qui ratione voluptatem</p>
    <a>READ MORE</a>
  </div>
</div>

<section class="services" role="img" aria-label="Dark background photo of a business meeting">
  <h2 class="section-title">Our Services</h2>
  <div class="service" style="left:126px;top:200px">
    <div class="diamond"><svg width="36" height="36" viewBox="0 0 36 36" fill="none" stroke="var(--orange)" stroke-width="2"><circle cx="18" cy="11" r="6"/><path d="M6 34V26a12 10 0 0124 0v8"/></svg></div>
    <div><h4>INDIVIDUALS</h4><p>Nemo enim ipsam voluptatem quia voluptas sit aspernatur aut odit aut fugit, sed quia consequuntur</p></div>
  </div>
  <div class="service" style="left:126px;top:390px">
    <div class="diamond"><svg width="36" height="36" viewBox="0 0 36 36" fill="none" stroke="var(--orange)" stroke-width="2"><circle cx="14" cy="22" r="9"/><path d="M24 6v28M24 6h8"/></svg></div>
    <div><h4>WORKPLACE RETIREMENT</h4><p>Nemo enim ipsam voluptatem quia voluptas sit aspernatur aut odit aut fugit, sed quia consequuntur</p></div>
  </div>
  <div class="center-ring"><span>Harlow Ridge Financial Partners</span></div>
  <div class="service" style="left:786px;top:200px">
    <div class="diamond"><svg width="36" height="36" viewBox="0 0 36 36" fill="none" stroke="var(--orange)" stroke-width="2"><path d="M4 30l10-10 6 6 12-14M24 12h8v8M4 34h28"/></svg></div>
    <div><h4>INTERMEDIARIES</h4><p>Nemo enim ipsam voluptatem quia voluptas sit aspernatur aut odit aut fugit, sed quia consequuntur</p></div>
  </div>
  <div class="service" style="left:786px;top:390px">
    <div class="diamond"><svg width="36" height="36" viewBox="0 0 36 36" fill="none" stroke="var(--orange)" stroke-width="2"><path d="M4 14L18 5l14 9M6 14h24M9 18v12M15 18v12M21 18v12M27 18v12M4 32h28"/></svg></div>
    <div><h4>INSTITUTIONS</h4><p>Nemo enim ipsam voluptatem quia voluptas sit aspernatur aut odit aut fugit, sed quia consequuntur</p></div>
  </div>
</section>

<h2 class="section-title" style="top:1993px">Our Projects</h2>
<span class="arrow-btn" style="left:49px"><svg width="48" height="48" viewBox="0 0 48 48" fill="none" stroke="#666" stroke-width="1.5"><path d="M27 16l-8 8 8 8"/></svg></span>
<span class="arrow-btn" style="left:1101px"><svg width="48" height="48" viewBox="0 0 48 48" fill="none" stroke="#666" stroke-width="1.5"><path d="M21 16l8 8-8 8"/></svg></span>
<div class="card" style="left:112px"><div class="photo" role="img" aria-label="Photo of colleagues reviewing a tablet" style="background:linear-gradient(135deg,#c49a6c,#8a6c50)"></div><p>Lorem ipsum dolor sit</p></div>
<div class="card" style="left:359px"><div class="photo" role="img" aria-label="Photo of financial charts and a calculator on a desk" style="background:linear-gradient(135deg,#e8eef2,#aab8c4)"></div><p>Lorem ipsum dolor sit</p></div>
<div class="card" style="left:605px"><div class="photo" role="img" aria-label="Photo of business people in a meeting room" style="background:linear-gradient(135deg,#dfe5ea,#6d7580)"></div><p>Lorem ipsum dolor sit</p></div>
<div class="card" style="left:851px"><div class="photo" role="img" aria-label="Photo of an advisor presenting documents to a client" style="background:linear-gradient(135deg,#d7d7d7,#6a6a6a)"></div><p>Lorem ipsum dolor sit</p></div>

<section class="help" role="img" aria-label="Photo of a team discussing work around a laptop">
  <div class="kicker">CAPITAL INVESTMENTS</div>
  <h2>WE ARE HERE TO HELP</h2>
  <p>Nemo enim ipsam voluptatem quia voluptas sit aspernatur aut odit aut fugit</p>
  <span class="btn">GET STARTED</span>
</section>

<h2 class="section-title" style="top:2928px">Partner Bios</h2>
<div class="bio-photo" role="img" aria-label="Portrait photo of a partner seated in an orange armchair" style="left:0;top:3018px;background:linear-gradient(120deg,#3a3a3a,#b06a2a 60%,#d08a3a)"></div>
<div class="bio right-accent" style="left:548px;top:3063px">
  <h3>Daniel Marsh</h3>
  <div class="role">Lorem ipsum dolor sit</div>
  <p>Nemo enim ipsam voluptatem quia voluptas sit aspernatur aut odit aut fugit, sed quia consequuntur magni dolores eos qui ratione voluptatem sequi nesciunt. Neque porro quisquam est, qui dolorem ipsum quia dolor sit amet, consectetur.</p>
  <div class="socials"><span></span><span></span><span></span><span></span></div>
</div>
<div class="bio-photo" role="img" aria-label="Portrait photo of a partner at a laptop in a brick office" style="left:600px;top:3406px;background:linear-gradient(120deg,#8a3a34,#c9c2b8 55%,#6a6a6a)"></div>
<div class="bio left-accent" style="left:112px;top:3448px">
  <h3>Elena Voss</h3>
  <div class="role">Lorem ipsum dolor sit</div>
  <p>Nemo enim ipsam voluptatem quia voluptas sit aspernatur aut odit aut fugit, sed quia consequuntur magni dolores eos qui ratione voluptatem sequi nesciunt. Neque porro quisquam est, qui dolorem ipsum quia dolor sit amet, consectetur.</p>
  <div class="socials"><span></span><span></span><span></span><span></span></div>
</div>

<section class="contact">
  <h2>GET IN TOUCH AND GET STARTED TODAY. WE'RE READY!</h2>
  <p class="lead">Nemo enim ipsam voluptatem quia voluptas sit aspernatur aut odit aut fugit, sed quia consequuntur magni dolores eos qui ratione voluptatem sequi nesciunt. Neque porro quisquam est, qui dolorem ipsum quia dolor sit amet, consectetur, adipisci velit.</p>
</section>
<div class="field" style="left:543px;top:3947px;width:262px">First Name</div>
<div class="field" style="left:825px;top:3947px;width:263px">Last Name</div>
<div class="field" style="left:543px;top:4030px;width:262px">Phone Number</div>
<div class="field" style="left:825px;top:4030px;width:263px">Email</div>
<div class="field" style="left:543px;top:4117px;width:262px">Job Tittle</div>
<div class="field" style="left:825px;top:4117px;width:263px">Company</div>
<div class="field" style="left:543px;top:4205px;width:545px;height:104px">Message</div>
<div class="forgot">Forgot Your Passsword ?</div>
<span class="btn submit">SUBMIT</span>

<footer class="footer">
  <h5 style="left:112px">QUICK LINKS</h5>
  <ul class="links" style="left:112px"><li>Home</li><li>About Us</li><li>Services</li><li>Projects</li><li>Partners</li><li>Contact</li></ul>
  <h5 style="left:326px">ABOUT</h5>
  <ul class="links" style="left:326px"><li>Team</li><li>News</li><li>Terms &amp; Condition</li><li>Privacy/Policy</li></ul>
  <h5 style="left:554px">CONTACT US</h5>
  <div class="c-item" style="top:148px"><span class="ring"><svg width="16" height="18" viewBox="0 0 16 18" fill="none" stroke="#ddd" stroke-width="1.5"><path d="M8 17s6-6 6-10A6 6 0 002 7c0 4 6 10 6 10z"/><circle cx="8" cy="7" r="2"/></svg></span><span>Nemo enim ipsam voluptatem quia voluptas sit</span></div>
  <div class="c-item" style="top:236px"><span class="ring"><svg width="16" height="16" viewBox="0 0 16 16" fill="none" stroke="#ddd" stroke-width="1.5"><path d="M3 1h3l1 4-2 1a9 9 0 005 5l1-2 4 1v3a2 2 0 01-2 2A13 13 0 011 3a2 2 0 012-2z"/></svg></span><span>555-014-2290</span></div>
  <div class="c-item" style="top:311px"><span class="ring"><svg width="18" height="14" viewBox="0 0 18 14" fill="none" stroke="#ddd" stroke-width="1.5"><rect x="1" y="1" width="16" height="12"/><path d="M1 1l8 7 8-7"/></svg></span><span>info@harlowridge.com</span></div>
  <h5 style="left:947px">CONNECT WITH US</h5>
  <div class="s-item" style="top:159px"><span class="ring"></span>Community</div>
  <div class="s-item" style="top:211px"><span class="ring"></span>Gallery</div>
  <div class="s-item" style="top:262px"><span class="ring"></span>Updates</div>
  <div class="s-item" style="top:314px"><span class="ring"></span>Network</div>
  <div class="copyright">© 2020 All Rights Reserved</div>
</footer>

</body>
</html>
```